Business cards - BRENT Roofing & Siding

We need simple business cards made up for our Roofing & Siding business based in Calgary Alberta.
The logo on one side of the card and potentially our slogan "Raised with care, proven by seasons".
The other side could have:
-A small logo
-Rep name:
-Rep cell phone:
-Rep email:
-Office phone: 403-684-2093
-Website: PrairieShingleWorks.com

We would like to incorporate the colours from our logo, especially the lite blue on the jpeg file. I have attached the ai file and jpeg file. We like the colours better on the jpeg file.

I do not require a money back guarantee

```html
<!DOCTYPE html>
<html lang="en">
<head>
<meta charset="utf-8">
<title>BRENT Roofing &amp; Siding – Business Cards</title>
<link rel="stylesheet" href="https://fonts.googleapis.com/css2?family=Lato:wght@400;700&display=swap">
<style>
  :root {
    --backdrop: #8e8e8e;
    --card-black: #000000;
    --card-white: #ffffff;
    --brand-blue: #1589ee;
    --deep-blue: #0a5fb4;
    --brand-red: #e4202a;
    --ink: #222222;
    --ink-soft: #3a3a3a;
  }
  * { margin: 0; padding: 0; box-sizing: border-box; }
  html, body { width: 1200px; height: 1122px; overflow: hidden; }
  body {
    background: var(--backdrop);
    font-family: "Lato", sans-serif;
    position: relative;
  }
  .card {
    position: absolute;
    width: 700px;
    height: 400px;
    border-radius: 26px;
    overflow: hidden;
    box-shadow: 0 14px 30px rgba(0,0,0,0.35);
  }

  /* Logo side */
  .card--logo {
    left: 70px; top: 70px;
    background: var(--card-black);
    display: flex; flex-direction: column; align-items: center; justify-content: center;
    gap: 70px;
  }
  .brand-mark { display: flex; align-items: center; gap: 16px; }
  .brand-mark__square { width: 34px; height: 34px; background: var(--brand-blue); flex: none; }
  .brand-mark__name {
    font-weight: 700; font-size: 44px; letter-spacing: 1px; color: var(--card-white);
    white-space: nowrap;
  }
  .slogan { font-weight: 700; font-size: 22px; letter-spacing: 1px; text-transform: uppercase; white-space: nowrap; }
  .slogan__lead { color: var(--brand-blue); }
  .slogan__close { color: var(--brand-red); }

  /* Contact side */
  .card--contact {
    left: 430px; top: 620px;
    background: var(--card-white);
  }
  .contact__brand {
    position: absolute; right: 42px; top: 48px;
    display: flex; align-items: center; gap: 12px;
  }
  .contact__brand .brand-mark__square { width: 24px; height: 24px; }
  .contact__brand .brand-mark__name { font-size: 30px; color: var(--ink); }
  .rule { position: absolute; height: 1.5px; background: var(--deep-blue); }
  .rule--top { right: 40px; top: 112px; width: 360px; }
  .rule--name { left: 44px; top: 236px; width: 250px; }
  .office {
    position: absolute; right: 42px; top: 126px; text-align: right;
    font-size: 17px; line-height: 1.4; color: var(--ink-soft); font-style: normal;
  }
  .office__company { color: var(--brand-blue); }
  .rep { position: absolute; left: 44px; top: 168px; }
  .rep__name { font-size: 34px; font-weight: 400; color: var(--brand-blue); letter-spacing: 0.5px; line-height: 1; white-space: nowrap; }
  .rep__title { font-size: 20px; color: var(--brand-red); margin-top: 6px; }
  .contact-list { position: absolute; left: 50px; top: 250px; list-style: none; }
  .contact-list li {
    display: flex; align-items: center; gap: 14px;
    font-size: 18px; color: var(--ink-soft); line-height: 30px; white-space: nowrap;
  }
  .contact-list svg { width: 16px; height: 16px; fill: var(--brand-blue); flex: none; }
  .footer-band { position: absolute; left: 0; bottom: 0; width: 700px; height: 44px; }
  .footer-band__site {
    position: absolute; right: 34px; bottom: 11px;
    color: var(--card-white); font-weight: 700; font-size: 17px; letter-spacing: 0.5px;
  }
</style>
</head>
<body>

<section class="card card--logo">
  <div class="brand-mark">
    <span class="brand-mark__square"></span>
    <span class="brand-mark__name">BRENT Roofing &amp; Siding</span>
  </div>
  <p class="slogan"><span class="slogan__lead">Raised with care,</span> <span class="slogan__close">proven by seasons</span></p>
</section>

<section class="card card--contact">
  <div class="contact__brand">
    <span class="brand-mark__square"></span>
    <span class="brand-mark__name">BRENT Roofing &amp; Siding</span>
  </div>
  <div class="rule rule--top"></div>

  <address class="office">
    <div class="office__company">BRENT Roofing &amp; Siding Ltd</div>
    <div>4820 - 9 Avenue S.E. Calgary</div>
    <div>Alberta T2B 3K7</div>
  </address>

  <div class="rep">
    <h1 class="rep__name">DALE WHITMORE</h1>
    <p class="rep__title">Managing Director</p>
  </div>
  <div class="rule rule--name"></div>

  <ul class="contact-list">
    <li>
      <svg viewBox="0 0 24 24" aria-hidden="true"><path d="M6.6 10.8a15.1 15.1 0 0 0 6.6 6.6l2.2-2.2c.3-.3.7-.4 1-.2 1.1.4 2.3.6 3.6.6.6 0 1 .4 1 1V20c0 .6-.4 1-1 1A17 17 0 0 1 3 4c0-.6.4-1 1-1h3.5c.6 0 1 .4 1 1 0 1.3.2 2.5.6 3.6.1.3 0 .7-.2 1z"/></svg>
      403-684-2093
    </li>
    <li>
      <svg viewBox="0 0 24 24" aria-hidden="true"><path d="M7 1h10a2 2 0 0 1 2 2v18a2 2 0 0 1-2 2H7a2 2 0 0 1-2-2V3a2 2 0 0 1 2-2zm0 3v14h10V4zm5 15.2a1.2 1.2 0 1 0 0 2.4 1.2 1.2 0 0 0 0-2.4z"/></svg>
      403-684-2093
    </li>
    <li>
      <svg viewBox="0 0 24 24" aria-hidden="true"><path d="M2 5h20v14H2zm2 2v.4l8 5.2 8-5.2V7zm0 2.8V17h16V9.8l-8 5.2z"/></svg>
      dale@prairieshingleworks.com
    </li>
  </ul>

  <svg class="footer-band" viewBox="0 0 700 44" preserveAspectRatio="none" aria-hidden="true">
    <polygon points="0,44 0,20 380,20 390,44" fill="var(--card-black)"/>
    <polygon points="360,44 380,0 700,0 700,44" fill="var(--brand-blue)"/>
  </svg>
  <span class="footer-band__site">www.PrairieShingleWorks.com</span>
</section>

</body>
</html>
```